Larkspur Talent IT Recruiting firm needs a business card design for Recruiters, Sourcers, and Account

We need business cards that allow us to change all contact info, names, titles (Recruiter, Sourcer, Account Manager, Director, CEO, etc) per person since we have three offices, in three cities, Phoenix, Austin, and Las Vegas. We do recruiting and contractors for IT positions (Developers, Architects, Software Engineers, Security Engineers, Help Desk, DBAs, PMs, Scrum Masters, etc.) Our client companies are very diverse from Meridian 100 to silicone Valley type start-ups.

So, while we what hip, techie, and quirky, it still needs to be professional. Primary color we use is blue, with silver as a secondary color.

Target Market(s)

IT, Technology

Industry/Entity Type

Business

Contact Information for Business Card

Company name: Larkspur Talent, Inc.
Website: www.larkspurtalent.example
Logos for Careerloop, Blipster, and Myriada

Name, Title, Office Number, Cell Number, email

Font styles to use
Serif
Sans Serif

Colors
0455a3
d5d5d5

Requirements
Nice to have
• The grey I selected below is not necessary - but, would like silver included. I included a card design (File 3: LTI early trial example.jpg) that I had started on. It's very rough, and not quite what we're looking for, but what we did like is the logo, big, maybe a bit faded, off center, goes out of frame, etc. Still looking for other ideas - you are the pros! But, just an idea of a design element we liked.

```html
<!DOCTYPE html>
<html lang="en">
<head>
<meta charset="utf-8">
<title>Larkspur Talent — Business Card</title>
<link rel="stylesheet" href="https://fonts.googleapis.com/css2?family=Marcellus&family=Open+Sans:wght@400;700&display=swap">
<style>
  :root {
    --backdrop: #3a3a3a;
    --card: #ffffff;
    --card-tint: #f4f4f4;
    --brand-blue: #1a8ad8;
    --deep-blue: #0455a3;
    --ink: #1b1b1b;
    --ink-soft: #333333;
    --silver: #d5d5d5;
  }
  * { box-sizing: border-box; margin: 0; padding: 0; }
  html, body { width: 1200px; height: 852px; overflow: hidden; }
  body {
    background: var(--backdrop);
    font-family: "Open Sans", Arial, sans-serif;
    position: relative;
  }
  .card {
    position: absolute;
    top: 289px;
    width: 490px;
    height: 280px;
    border-radius: 12px;
    background: linear-gradient(160deg, var(--card) 0%, var(--card-tint) 100%);
    overflow: hidden;
  }
  .card--front { left: 80px; }
  .card--back { left: 630px; }

  .wordmark {
    font-family: "Marcellus", Georgia, serif;
    color: var(--ink);
    letter-spacing: 0.04em;
    text-transform: uppercase;
    white-space: nowrap;
    line-height: 1;
  }
  .tagline {
    font-family: "Marcellus", Georgia, serif;
    color: var(--ink-soft);
    letter-spacing: 0.16em;
    text-transform: uppercase;
    white-space: nowrap;
  }

  /* Front */
  .card--front .brand {
    position: absolute;
    left: 0; right: 0; top: 100px;
    display: flex; flex-direction: column; align-items: center; gap: 24px;
  }
  .card--front .wordmark { font-size: 36px; }
  .card--front .tagline { font-size: 14px; }

  /* Back */
  .card--back .brand {
    position: absolute; left: 26px; top: 44px;
    display: flex; flex-direction: column; gap: 14px;
  }
  .card--back .wordmark { font-size: 26px; }
  .card--back .tagline { font-size: 10.5px; padding-left: 30px; }
  .rule {
    position: absolute; height: 2px; background: var(--brand-blue);
  }
  .rule--header { left: 26px; width: 260px; top: 118px; }
  .rule--contacts { left: 26px; width: 150px; top: 168px; height: 1.5px; }

  .person {
    position: absolute; right: 24px; top: 30px; text-align: right;
  }
  .person__name {
    font-weight: 700; color: var(--brand-blue); font-size: 14px; letter-spacing: 0.02em;
  }
  .person__title { font-size: 10px; color: var(--ink-soft); margin-top: 1px; }
  .social {
    display: flex; justify-content: flex-end; gap: 4px; margin-top: 8px;
  }
  .social__tile {
    width: 20px; height: 20px; border-radius: 3px; background: var(--brand-blue);
  }

  .contacts {
    position: absolute; left: 26px; top: 176px; list-style: none;
  }
  .contacts li {
    display: flex; align-items: center; gap: 10px;
    font-size: 11.5px; color: var(--ink); height: 16px;
  }
  .contacts svg { width: 11px; height: 11px; fill: var(--brand-blue); flex: none; }

  .address-band {
    position: absolute; left: 0; right: 0; bottom: 0; height: 36px;
    background: linear-gradient(90deg, var(--brand-blue), var(--deep-blue));
    color: #ffffff; font-size: 11.5px;
    display: flex; align-items: center; padding-left: 70px;
  }
</style>
</head>
<body>

  <section class="card card--front" aria-label="Card front">
    <div class="brand">
      <p class="wordmark">Larkspur Talent</p>
      <p class="tagline">Talent Meets the Moment</p>
    </div>
  </section>

  <section class="card card--back" aria-label="Card back">
    <div class="brand">
      <p class="wordmark">Larkspur Talent</p>
      <p class="tagline">Talent Meets the Moment</p>
    </div>
    <div class="rule rule--header"></div>

    <div class="person">
      <p class="person__name">DANA WHITCOMBE</p>
      <p class="person__title">CEO</p>
      <div class="social" aria-label="Blipster, Careerloop, Myriada">
        <span class="social__tile"></span>
        <span class="social__tile"></span>
        <span class="social__tile"></span>
      </div>
    </div>

    <div class="rule rule--contacts"></div>
    <ul class="contacts">
      <li>
        <svg viewBox="0 0 12 12" aria-hidden="true"><path d="M3 1 L5 3.5 L4 4.8 C4.6 6 6 7.4 7.2 8 L8.5 7 L11 9 L9.8 11 C5.5 10.6 1.4 6.5 1 2.2 Z"/></svg>
        <span>555| 210-4417</span>
      </li>
      <li>
        <svg viewBox="0 0 12 12" aria-hidden="true"><rect x="3" y="1" width="6" height="3"/><rect x="1" y="4.5" width="10" height="4.5" rx="1"/><rect x="3" y="8" width="6" height="3"/></svg>
        <span>555| 386-0925</span>
      </li>
      <li>
        <svg viewBox="0 0 12 12" aria-hidden="true"><path d="M1 3 H11 V10 H1 Z M1.5 3.5 L6 7 L10.5 3.5" stroke="#fff" stroke-width="0.8"/></svg>
        <span>dana@larkspurtalent.example</span>
      </li>
      <li>
        <svg viewBox="0 0 12 12" aria-hidden="true"><circle cx="6" cy="6" r="5"/><path d="M1 6 H11 M6 1 C3.5 4 3.5 8 6 11 M6 1 C8.5 4 8.5 8 6 11" stroke="#fff" stroke-width="0.7" fill="none"/></svg>
        <span>www.larkspurtalent.example</span>
      </li>
    </ul>

    <div class="address-band">4410 W Cedar Ave, Suite 210 Mesa Ridge, AZ 85000, USA</div>
  </section>

</body>
</html>
```